Business card - Harbor Crest Builders

Design a business card utilizing the given logo.
colors we like: Black, greys, Teal, blues.
Tri color card, horizontal orientation likely
Logo and name likely best on top.
Info on card:

Dennis Farrow
#8 - 4815 Alder Ridge Blvd.
Surrey, B.C. V3K 2R9

778.555.0193
dennisfarrow@tellmail.ca

Slogan: "Building Dreams"

We are a construction company that specializes in new home construction on the West coast of BC Canada. Open Concepts designs of high end homes.

```html
<!DOCTYPE html>
<html lang="en">
<head>
<meta charset="utf-8">
<title>Harbor Crest Builders — Business Card</title>
<link href="https://fonts.googleapis.com/css2?family=Questrial&family=Montserrat:wght@600&display=swap" rel="stylesheet">
<style>
  :root {
    --page: #e9e9e9;
    --card-light: #ffffff;
    --card-mid: #e6e6e6;
    --card-deep: #cfcfcf;
    --ink: #1a1a1a;
    --ink-soft: #3a3a3a;
    --rule: #8a8a8a;
    --teal: #2a8f98;
    --disc: #d6d6d6;
  }
  html, body {
    margin: 0;
    width: 1200px;
    height: 871px;
    overflow: hidden;
    background: var(--page);
  }
  .canvas {
    position: relative;
    width: 1200px;
    height: 871px;
  }
  .card {
    position: absolute;
    top: 287px;
    width: 520px;
    height: 297px;
    overflow: hidden;
    box-shadow: 0 6px 18px rgba(0,0,0,0.18);
    font-family: "Questrial", sans-serif;
    color: var(--ink);
  }
  .card--back {
    left: 50px;
    background: linear-gradient(160deg, var(--card-light) 0%, var(--card-mid) 60%, var(--card-deep) 100%);
  }
  .card--front {
    left: 630px;
    background: linear-gradient(165deg, var(--card-light) 0%, #f3f3f3 55%, var(--card-mid) 100%);
  }

  /* back side */
  .slogan-lockup {
    position: absolute;
    left: 0; right: 0;
    top: 126px;
    display: flex;
    align-items: center;
    justify-content: center;
    gap: 14px;
  }
  .mark-dot {
    width: 34px;
    height: 34px;
    border-radius: 50%;
    background: var(--ink);
    flex: none;
  }
  .divider {
    width: 1px;
    height: 44px;
    background: var(--rule);
    flex: none;
  }
  .slogan {
    color: var(--teal);
    font-size: 15px;
    letter-spacing: 2px;
  }

  /* front side */
  .decor-disc {
    position: absolute;
    left: -90px;
    top: 10px;
    width: 290px;
    height: 290px;
    border-radius: 50%;
    background: radial-gradient(circle at 55% 45%, #ececec 0%, var(--disc) 70%, #cacaca 100%);
    opacity: 0.7;
  }
  .holder-name {
    position: absolute;
    left: 58px;
    top: 140px;
    font-family: "Montserrat", sans-serif;
    font-weight: 600;
    font-size: 13px;
    letter-spacing: 2.5px;
    color: var(--ink);
  }
  .company-lockup {
    position: absolute;
    left: 262px;
    top: 74px;
    display: flex;
    align-items: center;
    gap: 10px;
  }
  .company-lockup .mark-dot { width: 28px; height: 28px; }
  .company-lockup .divider { height: 34px; }
  .company-name {
    font-size: 15px;
    letter-spacing: 1.5px;
    text-transform: uppercase;
    color: var(--ink);
  }
  .address {
    position: absolute;
    left: 262px;
    top: 160px;
    margin: 0;
    font-style: normal;
    font-size: 12px;
    line-height: 18px;
    letter-spacing: 1.6px;
    color: var(--ink-soft);
  }
  .contact {
    position: absolute;
    left: 262px;
    top: 210px;
    margin: 0;
    padding: 0;
    list-style: none;
    font-size: 12px;
    line-height: 18px;
    letter-spacing: 1.6px;
    color: var(--ink-soft);
  }
  .contact li {
    display: flex;
    align-items: center;
    gap: 8px;
  }
  .contact svg { flex: none; }
</style>
</head>
<body>
<main class="canvas">

  <section class="card card--back" aria-label="Card back">
    <div class="slogan-lockup">
      <span class="mark-dot" aria-hidden="true"></span>
      <span class="divider" aria-hidden="true"></span>
      <span class="slogan">Building Dreams</span>
    </div>
  </section>

  <section class="card card--front" aria-label="Card front">
    <div class="decor-disc" aria-hidden="true"></div>
    <div class="holder-name">Dennis Farrow</div>

    <div class="company-lockup">
      <span class="mark-dot" aria-hidden="true"></span>
      <span class="divider" aria-hidden="true"></span>
      <span class="company-name">Harbor Crest Builders</span>
    </div>

    <address class="address">
      #8 - 4815 Alder Ridge Blvd.<br>
      Surrey, B.C. V3K 2R9
    </address>

    <ul class="contact">
      <li>
        <svg width="10" height="10" viewBox="0 0 10 10" aria-hidden="true">
          <path d="M2 1 L4 1 L4.6 3 L3.4 4 C4 5.3 4.7 6 6 6.6 L7 5.4 L9 6 L9 8 C9 8.6 8.6 9 8 9 C4.2 9 1 5.8 1 2 C1 1.4 1.4 1 2 1 Z" fill="var(--teal)"/>
        </svg>
        <span>778.555.0193</span>
      </li>
      <li>
        <svg width="10" height="10" viewBox="0 0 10 10" aria-hidden="true">
          <rect x="0.5" y="2" width="9" height="6" fill="none" stroke="var(--teal)" stroke-width="1"/>
          <path d="M0.5 2 L5 5.5 L9.5 2" fill="none" stroke="var(--teal)" stroke-width="1"/>
        </svg>
        <span>dennisfarrow@tellmail.ca</span>
      </li>
    </ul>
  </section>

</main>
</body>
</html>
```